Business Card Design Project

After recently finishing a design project for the company logo using markbazaar, it's now time for a business card. Attached to this is the logo.

The requirements for the business card are pretty straightforward:

- A clean, uncomplicated look
- Consistent usage of fonts
- Designs for both single sided and double sided cards
- A modern layout with preferably space to refer to social media accounts and/or downloadable vcards through a qr code
- consistent application of the company colour scheme: red/white. Hex codes for exact colour can be provided

Thanks!

```html
<!DOCTYPE html>
<html lang="en">
<head>
<meta charset="utf-8">
<title>Kiln Row Staffing – Business Card</title>
<link rel="stylesheet" href="https://fonts.googleapis.com/css2?family=Open+Sans:ital,wght@0,400;0,600;0,700;1,700&display=swap">
<style>
  :root {
    --brand-red: #e31e26;
    --ink: #231f20;
    --slate: #858585;
    --paper: #ffffff;
    --backdrop: #e8e5e1;
  }
  * { margin: 0; padding: 0; box-sizing: border-box; }
  html, body {
    width: 960px;
    height: 1200px;
    overflow: hidden;
  }
  body {
    position: relative;
    background: var(--backdrop);
    font-family: "Open Sans", Arial, sans-serif;
    color: var(--ink);
  }
  .card {
    position: absolute;
    width: 840px;
    height: 480px;
    background: var(--paper);
    border-radius: 28px;
    overflow: hidden;
  }
  .card--front { left: 58px; top: 70px; }
  .card--back  { left: 60px; top: 638px; }

  .wordmark {
    position: absolute;
    left: 32px;
    top: 56px;
    display: flex;
    align-items: center;
    gap: 26px;
  }
  .wordmark__square {
    width: 104px;
    height: 104px;
    background: var(--brand-red);
  }
  .wordmark__name {
    font-size: 62px;
    font-weight: 600;
    color: var(--ink);
    letter-spacing: -1px;
    white-space: nowrap;
  }

  .name-band {
    position: absolute;
    left: 540px;
    top: 232px;
    width: 300px;
    height: 81px;
    display: flex;
  }
  .name-band__label {
    width: 254px;
    background: var(--brand-red);
    color: var(--paper);
    padding: 12px 0 0 20px;
  }
  .name-band__tab {
    flex: 1;
    background: var(--slate);
  }
  .person-name {
    font-size: 26px;
    font-weight: 700;
    line-height: 34px;
  }
  .person-role {
    font-size: 20px;
    font-weight: 400;
    line-height: 26px;
  }

  .contact-list {
    position: absolute;
    left: 560px;
    top: 352px;
    list-style: none;
    font-size: 20px;
    line-height: 34.5px;
  }
  .contact-list b {
    font-style: italic;
    font-weight: 700;
  }

  .address {
    position: absolute;
    left: 40px;
    top: 397px;
    font-size: 20px;
    line-height: 28px;
    font-style: normal;
  }

  .back-mark {
    position: absolute;
    inset: 0;
    display: flex;
    align-items: center;
    justify-content: center;
    gap: 24px;
  }
  .back-mark__square {
    width: 90px;
    height: 90px;
    background: var(--brand-red);
  }
  .back-mark__name {
    font-size: 54px;
    font-weight: 600;
    color: var(--brand-red);
    letter-spacing: -1px;
    white-space: nowrap;
  }
</style>
</head>
<body>
  <section class="card card--front" aria-label="Business card front">
    <div class="wordmark">
      <span class="wordmark__square" aria-hidden="true"></span>
      <span class="wordmark__name">Kiln Row Staffing</span>
    </div>

    <div class="name-band">
      <div class="name-band__label">
        <p class="person-name">Your Name</p>
        <p class="person-role">Designation</p>
      </div>
      <div class="name-band__tab"></div>
    </div>

    <ul class="contact-list">
      <li><b>t</b> : 123-123-1234</li>
      <li><b>e</b> : info@yourwebsite.com</li>
      <li><b>w</b> : www.kilnrowstaffing.com</li>
    </ul>

    <address class="address">
      1234, Street Name<br>
      District, City, Country Code.
    </address>
  </section>

  <section class="card card--back" aria-label="Business card back">
    <div class="back-mark">
      <span class="back-mark__square" aria-hidden="true"></span>
      <span class="back-mark__name">Kiln Row Staffing</span>
    </div>
  </section>
</body>
</html>
```